English and Spanish Language School Needs a Business Card

Need a business card design a startup company called Maribel Language School. The company will offer English and Spanish conversational level courses designed to make the learner feel comfortable with grammar and vocabulary. We would like to see a logo with some colour that should communicate learning, growth.

Target Market(s)

Consumers and businesses

Industry/Entity Type

Education

Contact Information for Business Card

TBD

Font styles to use
Serif

Requirements
Must have
• Include the following
• Logo
• Name
• Title
• Cellphone Number
• Office Phone number
• Email address
• Office Address

```html
<!DOCTYPE html>
<html lang="en">
<head>
<meta charset="utf-8">
<title>Maribel Language School — Business Card</title>
<link href="https://fonts.googleapis.com/css2?family=Source+Serif+4:wght@400;600;700&display=swap" rel="stylesheet">
<style>
  :root {
    --page-bg: #e9e7e5;
    --card-top: #f7f5f4;
    --band-red: #7c0d12;
    --accent-teal: #2bb5c8;
    --text-light: #ffffff;
    --divider: rgba(255, 255, 255, 0.45);
  }
  * { margin: 0; padding: 0; box-sizing: border-box; }
  html, body {
    width: 1200px;
    height: 900px;
    overflow: hidden;
    background: var(--page-bg);
    font-family: "Source Serif 4", serif;
  }
  .business-card {
    position: absolute;
    left: 100px;
    top: 140px;
    width: 1000px;
    height: 619px;
    background: var(--card-top);
    box-shadow: 0 10px 30px rgba(0, 0, 0, 0.12);
    overflow: hidden;
  }
  .brand-area {
    position: absolute;
    left: 0;
    top: 0;
    width: 100%;
    height: 312px;
    display: flex;
    align-items: center;
    justify-content: center;
  }
  .brand-name {
    color: var(--band-red);
    font-size: 66px;
    font-weight: 600;
    line-height: 1;
    white-space: nowrap;
  }

  .contact-band {
    position: absolute;
    left: 0;
    top: 312px;
    width: 100%;
    height: 307px;
    background: var(--band-red);
    color: var(--text-light);
  }
  .person {
    position: absolute;
    left: 98px;
    top: 122px;
    width: 270px;
  }
  .person-name { font-size: 32px; font-weight: 700; line-height: 1.1; white-space: nowrap; }
  .person-title { font-size: 27px; font-weight: 400; line-height: 1.25; }
  .band-divider {
    position: absolute;
    left: 384px;
    top: 65px;
    width: 2px;
    height: 198px;
    background: var(--divider);
  }
  .contact-list {
    position: absolute;
    left: 424px;
    top: 76px;
    font-size: 27px;
    line-height: 41px;
    white-space: nowrap;
  }
  .contact-label { color: var(--accent-teal); }
  .contact-gap { display: inline-block; width: 30px; }
  .address { margin-top: 22px; line-height: 36px; }
</style>
</head>
<body>
  <main class="business-card">
    <section class="brand-area">
      <p class="brand-name">Maribel Language School</p>
    </section>
    <section class="contact-band">
      <div class="person">
        <p class="person-name">Julien Marchand</p>
        <p class="person-title">President</p>
      </div>
      <div class="band-divider" aria-hidden="true"></div>
      <div class="contact-list">
        <p><span class="contact-label">Tel:</span> 514-555-018<span class="contact-gap"></span><span class="contact-label">Mob:</span> 5555-210-48</p>
        <p><span class="contact-label">E-mail:</span> info@maribelschool.com</p>
        <p class="address">4350 Rue des Érables<br>Montreal, QC H2K3B9</p>
      </div>
    </section>
  </main>
</body>
</html>
```